Shine Fox Auto Care Business Card

2 side business card design for an auto detailing business

Target Market(s)

Auto detailing

Contact Information for Business Card

Things included

The business name “Shine Fox Auto Care”
Mark Dunrow
(403)271-6094
Westbrook, Sk

Services offered - complete interior& exterior detail
- paint correction & protection
- ceramic coating
- trim restore
- auto carpet & seat cleaning

Requirements
Must have
• Colours that are in my logo

Services offered

My name Mark Dunrow
403-271-6094
Westbrook, Sk

Not too sure in what order for these ?
Website. Shinefoxautocare.com
Instagram Shinefoxautocare
Email. Shinefoxautoac@mailvento.com

```html
<!DOCTYPE html>
<html lang="en">
<head>
<meta charset="utf-8">
<title>Shine Fox Auto Care – Business Card</title>
<link rel="stylesheet" href="https://fonts.googleapis.com/css2?family=Montserrat:wght@400;500;600;700&display=swap">
<style>
  :root {
    --bg: #8a8a8a;
    --brand-red: #960000;
    --charcoal: #231f20;
    --white: #ffffff;
    --ink: #111111;
  }
  * { margin: 0; padding: 0; box-sizing: border-box; }
  html, body { width: 1200px; height: 1200px; overflow: hidden; }
  body {
    background: var(--bg);
    font-family: "Montserrat", sans-serif;
    position: relative;
  }
  .card {
    position: absolute;
    left: 150px;
    width: 900px;
    height: 514px;
    border-radius: 24px;
    overflow: hidden;
  }
  .card-front { top: 56px; background: var(--brand-red); }
  .card-back { top: 630px; background: var(--white); }

  .front-strip {
    position: absolute;
    top: 0; right: 0;
    width: 294px; height: 100%;
    background: var(--charcoal);
  }
  .front-badge {
    position: absolute;
    left: 358px; top: 1px;
    width: 508px; height: 508px;
    border-radius: 50%;
    background: var(--white);
    display: flex;
    align-items: center;
    justify-content: center;
    text-align: center;
  }
  .front-badge .brand-name {
    color: var(--brand-red);
    font-weight: 700;
    font-size: 54px;
    line-height: 1.15;
    letter-spacing: 1px;
    text-transform: uppercase;
    width: 360px;
  }

  .contact { position: absolute; left: 46px; color: var(--white); }
  .owner-name {
    top: 66px;
    font-size: 29px;
    font-weight: 500;
    letter-spacing: 1px;
    text-transform: uppercase;
  }
  .location { top: 118px; font-size: 20px; font-weight: 500; }
  .phone { top: 142px; font-size: 27px; font-weight: 600; }
  .divider {
    position: absolute;
    left: 53px; top: 214px;
    width: 122px; height: 2px;
    background: var(--white);
  }
  .services-heading {
    top: 260px;
    font-size: 20px;
    font-weight: 700;
    line-height: 25px;
    text-transform: uppercase;
  }
  .services-list {
    top: 314px;
    list-style: none;
    font-size: 20px;
    font-weight: 500;
    line-height: 25.5px;
    letter-spacing: 0.3px;
  }
  .services-list li { position: relative; padding-left: 18px; }
  .services-list li::before {
    content: "";
    position: absolute;
    left: 1px; top: 10px;
    width: 8px; height: 8px;
    border-radius: 50%;
    background: var(--white);
  }

  .back-lockup {
    position: absolute;
    left: 0; right: 0;
    top: 136px;
    display: flex;
    flex-direction: column;
    align-items: center;
  }
  .back-mark {
    width: 146px; height: 146px;
    border-radius: 50%;
    border: 16px solid var(--brand-red);
  }
  .back-lockup .brand-name {
    margin-top: 26px;
    color: var(--ink);
    font-weight: 600;
    font-size: 40px;
    letter-spacing: 2px;
    text-transform: uppercase;
  }
</style>
</head>
<body>
  <section class="card card-front" aria-label="Business card front">
    <div class="front-strip"></div>
    <div class="front-badge"><span class="brand-name">Shine Fox Auto Care</span></div>

    <p class="contact owner-name">Mark Dunrow</p>
    <p class="contact location">Westbrook, Sk</p>
    <p class="contact phone">(403)271-6094</p>
    <div class="divider"></div>
    <p class="contact services-heading">Complete Interior<br>&amp; Exterior Detail</p>
    <ul class="contact services-list">
      <li>Paint correction<br>&amp; Protection</li>
      <li>Ceramic coating</li>
      <li>Trim restore</li>
      <li>Auto carpet &amp; Seat cleaning</li>
    </ul>
  </section>

  <section class="card card-back" aria-label="Business card back">
    <div class="back-lockup">
      <div class="back-mark"></div>
      <p class="brand-name">Shine Fox Auto Care</p>
    </div>
  </section>
</body>
</html>
```